Icons/images for company values

We have five company values, we have a new logo and a new look. I would like drawn images for each value that are in keeping with our look and feel.

Target Market(s)

internal/staff

Industry/Entity Type

media compliance

Requirements
Must have
• colours aligned with logo.

```html
<!DOCTYPE html>
<html lang="en">
<head>
<meta charset="utf-8">
<title>Values 2023</title>
<link rel="stylesheet" href="https://fonts.googleapis.com/css2?family=Poppins:wght@200;400;800&display=swap">
<style>
  :root {
    --navy: #0a4058;
    --white: #ffffff;
    --ink: #2a2a2a;
    --icon: #3b3b3b;
    --yellow: #f3d63f;
    --yellow-deep: #c2a632;
    --lime: #b6e26c;
    --lime-deep: #98c14e;
    --deep: #0b4f6c;
    --deep-text: #0b4a69;
    --teal: #25a3c6;
    --teal-text: #1ea0c6;
    --blue: #0f76b5;
    --blue-text: #0f77b8;
  }
  * { margin: 0; padding: 0; box-sizing: border-box; }
  html, body { width: 1200px; height: 1080px; overflow: hidden; }
  body { font-family: "Poppins", sans-serif; background: var(--navy); }

  .canvas { position: relative; width: 1200px; height: 1080px; overflow: hidden; }
  .band-top { position: absolute; left: 0; top: 0; width: 1200px; height: 500px; background: var(--navy); }
  .band-bottom {
    position: absolute; left: 0; top: 500px; width: 1200px; height: 580px;
    background: linear-gradient(60deg, #0c6a9a 0%, #1190d8 40%, #49c9b4 68%, #7ef29a 88%, #b4e676 100%);
  }

  .brand {
    position: absolute; left: 96px; top: 145px;
    display: flex; align-items: center; gap: 12px;
    font-weight: 400; font-size: 34px; letter-spacing: 0.28em; color: var(--white);
  }
  .brand-mark { width: 14px; height: 14px; background: var(--white); }

  .title {
    position: absolute; left: 312px; top: 92px;
    display: flex; align-items: baseline; gap: 24px; line-height: 1;
  }
  .title-main { font-weight: 800; font-size: 128px; color: var(--white); letter-spacing: 0.01em; }
  .title-year { font-weight: 200; font-size: 120px; color: var(--yellow); letter-spacing: 0.1em; }

  .value {
    position: absolute; top: 372px; width: 192px; height: 584px;
    background: var(--white); border-radius: 96px;
    text-align: center;
  }
  .value-1 { left: 89px; }
  .value-2 { left: 297px; }
  .value-3 { left: 505px; }
  .value-4 { left: 713px; }
  .value-5 { left: 921px; }

  .value-number {
    position: absolute; left: -10px; top: -48px;
    font-weight: 800; font-size: 100px; line-height: 1;
  }
  .value-ring {
    position: absolute; left: 8px; top: 8px; width: 176px; height: 176px;
    border-radius: 50%; border: 16px solid; background: var(--white);
    box-shadow: 0 6px 14px rgba(0,0,0,0.2);
    display: flex; align-items: center; justify-content: center;
  }
  .value-ring svg { width: 74px; height: 74px; }
  .icon-area { width: 76px; height: 76px; border-radius: 50%; }

  .value-title {
    position: absolute; left: 12px; right: 12px; top: 246px;
    font-weight: 800; font-size: 15.5px; line-height: 18px; text-transform: uppercase;
  }
  .value-text {
    position: absolute; left: 18px; right: 18px; top: 360px;
    font-weight: 400; font-size: 12.5px; line-height: 15.5px; color: var(--ink);
  }

  .value-1 .value-number { color: var(--yellow); }
  .value-1 .value-ring { border-color: var(--yellow); }
  .value-1 .value-title { color: var(--yellow-deep); }
  .value-1 .icon-area { background: radial-gradient(circle, #c2a632 0 30%, #3b3b3b 32% 100%); }

  .value-2 .value-number { color: var(--lime); }
  .value-2 .value-ring { border-color: var(--lime); }
  .value-2 .value-title { color: var(--lime-deep); }
  .value-2 .icon-area { background: radial-gradient(circle, #98c14e 0 25%, #3b3b3b 27% 100%); }

  .value-3 .value-number { color: var(--deep); }
  .value-3 .value-ring { border-color: var(--deep); }
  .value-3 .value-title { color: var(--deep-text); }

  .value-4 .value-number { color: var(--teal); }
  .value-4 .value-ring { border-color: var(--teal); }
  .value-4 .value-title { color: var(--teal-text); }

  .value-5 .value-number { color: var(--blue); }
  .value-5 .value-ring { border-color: var(--blue); }
  .value-5 .value-title { color: var(--blue-text); }
</style>
</head>
<body>
<main class="canvas">
  <div class="band-top"></div>
  <div class="band-bottom"></div>

  <div class="brand"><span class="brand-name">KLARO</span><span class="brand-mark"></span></div>

  <h1 class="title"><span class="title-main">VALUES</span><span class="title-year">2023</span></h1>

  <section class="value value-1">
    <div class="value-number">1</div>
    <div class="value-ring">
      <div class="icon-area" role="img" aria-label="Icon of two open hands holding a heart"></div>
    </div>
    <h2 class="value-title">We're open<br>&amp; honest</h2>
    <p class="value-text">Sharing information helps us achieve the best outcomes for our teams and business. We value open, honest, and clear communication.</p>
  </section>

  <section class="value value-2">
    <div class="value-number">2</div>
    <div class="value-ring">
      <div class="icon-area" role="img" aria-label="Icon of two colleagues giving a high five"></div>
    </div>
    <h2 class="value-title">We get there<br>faster,<br>together</h2>
    <p class="value-text">Collaboration is at the heart of what we do, no matter our team.</p>
  </section>

  <section class="value value-3">
    <div class="value-number">3</div>
    <div class="value-ring">
      <svg viewBox="0 0 74 74" aria-label="Light bulb with shield icon" role="img">
        <path d="M37 4a24 24 0 0 0-14 43.5V54h28v-6.5A24 24 0 0 0 37 4z" fill="var(--icon)"/>
        <rect x="25" y="57" width="24" height="4" rx="2" fill="var(--icon)"/>
        <rect x="27" y="63" width="20" height="4" rx="2" fill="var(--icon)"/>
        <path d="M32 69h10l-2 4h-6z" fill="var(--icon)"/>
        <path d="M37 14l12 4v9c0 9-6 14-12 16-6-2-12-7-12-16v-9z" fill="var(--white)"/>
        <path d="M37 18l8 3v6c0 6-4 10-8 11.5-4-1.5-8-5.5-8-11.5v-6z" fill="var(--deep)"/>
      </svg>
    </div>
    <h2 class="value-title">We are leaders<br>in copyright<br>&amp; intellectual<br>property</h2>
    <p class="value-text">Leading the conversation in audio-visual copyright compliance and advocating for the protection of intellectual property globally.</p>
  </section>

  <section class="value value-4">
    <div class="value-number">4</div>
    <div class="value-ring">
      <svg viewBox="0 0 74 74" aria-label="Envelope with verified badge icon" role="img">
        <rect x="4" y="10" width="54" height="44" rx="5" fill="var(--icon)"/>
        <path d="M11 22l20 10 20-10" stroke="var(--white)" stroke-width="5" fill="none" stroke-linejoin="round"/>
        <circle cx="54" cy="52" r="17" fill="var(--white)"/>
        <path d="M54 38l4 3 5-1 1 5 4 3-2 5 2 5-4 3-1 5-5-1-4 3-4-3-5 1-1-5-4-3 2-5-2-5 4-3 1-5 5 1z" fill="var(--teal)"/>
        <path d="M47 52l5 5 9-9" stroke="var(--white)" stroke-width="3.5" fill="none" stroke-linecap="round" stroke-linejoin="round"/>
      </svg>
    </div>
    <h2 class="value-title">We get<br>things done</h2>
    <p class="value-text">We grow through capability, focus and hard work. We believe small steps compound to big results.</p>
  </section>

  <section class="value value-5">
    <div class="value-number">5</div>
    <div class="value-ring">
      <svg viewBox="0 0 74 74" aria-label="Clipboard with tick icon" role="img">
        <rect x="14" y="12" width="46" height="58" rx="3" fill="var(--icon)"/>
        <rect x="26" y="7" width="22" height="10" rx="3" fill="var(--blue)"/>
        <circle cx="37" cy="6" r="5" fill="var(--blue)"/>
        <path d="M25 42l8 8 16-17" stroke="var(--white)" stroke-width="6" fill="none" stroke-linecap="round" stroke-linejoin="round"/>
      </svg>
    </div>
    <h2 class="value-title">Diverse<br>perspectives<br>build better<br>outcomes</h2>
    <p class="value-text">We value diversity, inclusion, respect and trust within our teams. We are building a truly global organisation.</p>
  </section>
</main>
</body>
</html>
```